Corvena Hotel, city center modern minimal hotel operating all year round, on Rhodes island Greece

city, modern ,all year operating hotel

Target Market(s)

tourists, business agents

Industry/Entity Type

tourism

Number of Pages Required

2 page

Requirements
Must have
• room type photos and descriptions, amenities individual listing (graphic), comments sections, map driving location details
Nice to have
• gallery section, modern and minimal design, amenities section, individual room type descriptions, photos and facilities

```html
<!DOCTYPE html>
<html lang="en">
<head>
<meta charset="utf-8">
<title>Contact Us – Corvena Hotel</title>
<link href="https://fonts.googleapis.com/css2?family=Jost:wght@400;500&family=Barlow:wght@400;500;600&display=swap" rel="stylesheet">
<style>
:root{
  --gold:#bf9a47;
  --ink:#1b1b1b;
  --body:#2c2c2c;
  --muted:#666;
  --line:#e3e3e3;
  --footer:#0f1318;
  --footer-line:#252a30;
  --white:#fff;
}
*{box-sizing:border-box;margin:0;padding:0}
html,body{width:671px;height:1200px;overflow:hidden;background:var(--white)}
body{font-family:"Barlow",sans-serif;color:var(--body)}
.page{position:relative;width:1366px;height:2442px;transform:scale(0.4912);transform-origin:0 0}
.abs{position:absolute}

/* hero */
.hero{left:0;top:0;width:1366px;height:451px;background:radial-gradient(ellipse at 75% 30%,#3d3a36 0%,#26221f 45%,#1b1815 100%)}
.hero-divider{left:0;top:119px;width:1366px;height:1px;background:rgba(255,255,255,.15)}
.brand{left:58px;top:34px;display:flex;align-items:center;gap:14px}
.brand-square{width:30px;height:30px;background:var(--gold)}
.brand-name{font-family:"Jost",sans-serif;font-size:34px;font-weight:400;color:var(--white);letter-spacing:1px}
.nav{left:377px;top:47px;display:flex;gap:56px;font-family:"Jost",sans-serif;font-size:19px;font-weight:500;color:var(--white)}
.nav span sup{font-size:15px;margin-left:6px;vertical-align:0}
.btn{background:var(--gold);color:var(--white);font-family:"Barlow",sans-serif;font-weight:600;font-size:17px;text-transform:uppercase;display:flex;align-items:center;justify-content:center;gap:12px}
.book{left:1085px;top:30px;width:202px;height:60px}
.hero-title{left:0;width:1366px;top:236px;text-align:center;font-family:"Jost",sans-serif;font-size:46px;font-weight:400;color:var(--white)}
.crumbs{left:0;width:1366px;top:304px;text-align:center;font-size:15px;font-weight:600;color:var(--white)}
.crumbs em{font-style:normal;color:var(--gold);font-weight:500}

/* contact */
.h2{font-family:"Jost",sans-serif;font-size:30px;font-weight:400;color:var(--ink)}
.touch-title{left:125px;top:572px}
.intro{left:125px;top:638px;width:460px;font-size:15px;line-height:26px}
.info{left:125px;display:flex;gap:22px}
.info svg{flex:none;margin-top:2px}
.info .label{font-size:16px;color:var(--muted);margin-bottom:8px}
.info .value{font-family:"Jost",sans-serif;font-size:18px;color:var(--ink);line-height:28px}
.socials{left:125px;top:1013px;display:flex;gap:13px}
.socials span{width:40px;height:40px;border:1px solid var(--line);border-radius:50%}
.mass-title{left:600px;top:572px}
.field{border:1px solid var(--line);height:60px;display:flex;align-items:center;gap:10px;padding-left:18px;font-size:14px;color:var(--muted)}
.textarea{left:600px;top:826px;width:641px;height:220px;align-items:flex-start;padding-top:20px}
.submit{left:600px;top:1083px;width:218px;height:60px}
.map{left:125px;top:1263px;width:1116px;height:570px;background:linear-gradient(135deg,#d8d8d8,#c4c4c4 55%,#d2d2d2)}

/* footer */
.footer{left:0;top:1953px;width:1366px;height:489px;background:var(--footer);color:#d6d6d6}
.f-brand{left:125px;top:2030px}
.f-about{left:125px;top:2104px;width:250px;font-size:15px;line-height:28px;color:#d6d6d6}
.f-socials{left:125px;top:2184px}
.f-socials span{border-color:var(--footer-line)}
.f-head{font-family:"Jost",sans-serif;font-size:20px;font-weight:500;color:var(--white);top:2045px}
.f-info{left:410px;top:2106px;font-size:15px;color:#e2e2e2}
.f-info div{display:flex;gap:18px;align-items:flex-start;margin-bottom:18px;line-height:24px}
.f-links{left:697px;top:2106px;font-size:15px;line-height:36px;color:#e2e2e2}
.sub-field{left:885px;top:2108px;width:286px;height:70px;border:1px solid var(--footer-line);border-right:0;padding-left:20px;display:flex;align-items:center;font-size:15px;color:#8a8e93}
.sub-btn{left:1171px;top:2108px;width:70px;height:70px;background:var(--gold);display:flex;align-items:center;justify-content:center}
.bottom-line{left:0;top:2335px;width:1366px;height:1px;background:var(--footer-line)}
.copy{left:125px;top:2380px;font-size:15px;color:var(--white)}
.copy em{font-style:normal;color:var(--gold)}
.legal{right:125px;top:2380px;font-size:15px;color:var(--white);display:flex;gap:16px}
.legal i{font-style:normal;color:#555}
.to-top{left:1297px;top:2373px;width:48px;height:48px;border:2px solid var(--gold);border-radius:50%;display:flex;align-items:center;justify-content:center}
</style>
</head>
<body>
<div class="page">

  <header>
    <div class="abs hero" role="img" aria-label="Photo of a dim hotel room with a sofa, patterned cushions and a fur rug"></div>
    <div class="abs hero-divider"></div>
    <div class="abs brand"><span class="brand-square"></span><span class="brand-name">Corvena Hotel</span></div>
    <nav class="abs nav">
      <span>Home<sup>+</sup></span><span>Pages<sup>+</sup></span><span>Room<sup>+</sup></span><span>Blog<sup>+</sup></span><span>Contact</span>
    </nav>
    <a class="abs btn book">Book Now
      <svg width="18" height="12" viewBox="0 0 18 12"><path d="M0 6h16M11 1l5 5-5 5" fill="none" stroke="#fff" stroke-width="1.8"/></svg></a>
    <h1 class="abs hero-title">Contact Us</h1>
    <div class="abs crumbs">Home&nbsp; - &nbsp;<em>Contact Us</em></div>
  </header>

  <section>
    <h2 class="abs h2 touch-title">Get In Touch</h2>
    <p class="abs intro">Phasellus nisi sapien, rutrum placerat sapien eu, rhoncus tempus felis. Nulla non pulvinar enim, vel viverra nunc</p>

    <div class="abs info" style="top:722px">
      <svg width="32" height="32" viewBox="0 0 32 32"><path d="M8 3l5 7-3 3c2 4 5 7 9 9l3-3 7 5-3 4C15 27 5 17 4 6z" fill="none" stroke="#bf9a47" stroke-width="1.6"/></svg>
      <div><div class="label">Emergency Help</div><div class="value">+30 ( 224 ) 105 5896</div></div>
    </div>
    <div class="abs info" style="top:806px">
      <svg width="32" height="32" viewBox="0 0 32 32"><rect x="1" y="7" width="30" height="20" fill="none" stroke="#bf9a47" stroke-width="1.6"/><path d="M1 8l15 11L31 8" fill="none" stroke="#bf9a47" stroke-width="1.6"/></svg>
      <div><div class="label">Quick Email</div><div class="value">support@corvenahotel.gr</div></div>
    </div>
    <div class="abs info" style="top:890px;gap:24px">
      <svg width="24" height="34" viewBox="0 0 24 34"><path d="M12 33C4 22 1 16 1 12a11 11 0 0122 0c0 4-3 10-11 21z" fill="none" stroke="#bf9a47" stroke-width="1.6"/><circle cx="12" cy="12" r="4" fill="none" stroke="#bf9a47" stroke-width="1.6"/></svg>
      <div><div class="label">Office Address</div><div class="value">14 Iroon Polytechniou<br>Rhodes, Greece</div></div>
    </div>
    <div class="abs socials"><span></span><span></span><span></span><span></span></div>

    <h2 class="abs h2 mass-title">Send Massage</h2>
    <div class="abs field" style="left:600px;top:646px;width:309px">
      <svg width="16" height="16" viewBox="0 0 16 16"><circle cx="8" cy="5" r="3.5" fill="none" stroke="#bf9a47" stroke-width="1.3"/><path d="M1.5 15c0-4 3-6 6.5-6s6.5 2 6.5 6z" fill="none" stroke="#bf9a47" stroke-width="1.3"/></svg>Full Name</div>
    <div class="abs field" style="left:933px;top:646px;width:308px">
      <svg width="16" height="16" viewBox="0 0 16 16"><path d="M1 7l7-5 7 5v8H1z M1 7l7 5 7-5" fill="none" stroke="#bf9a47" stroke-width="1.3"/></svg>Email Address</div>
    <div class="abs field" style="left:600px;top:736px;width:309px">
      <svg width="16" height="16" viewBox="0 0 32 32"><path d="M8 3l5 7-3 3c2 4 5 7 9 9l3-3 7 5-3 4C15 27 5 17 4 6z" fill="none" stroke="#bf9a47" stroke-width="2.6"/></svg>Phone</div>
    <div class="abs field" style="left:933px;top:736px;width:308px">
      <svg width="16" height="16" viewBox="0 0 16 16"><rect x="2" y="1" width="12" height="14" fill="none" stroke="#bf9a47" stroke-width="1.3"/><circle cx="8" cy="6" r="2" fill="none" stroke="#bf9a47" stroke-width="1.3"/><path d="M5 12c0-2 6-2 6 0" fill="none" stroke="#bf9a47" stroke-width="1.3"/></svg>Subject</div>
    <div class="abs field textarea">
      <svg width="18" height="16" viewBox="0 0 18 16"><path d="M1 2h11v7H5l-3 3V9H1z M13 5h4v7h-1v3l-3-3H7" fill="none" stroke="#bf9a47" stroke-width="1.3"/></svg>Type your comments....</div>
    <a class="abs btn submit">Submit Now
      <svg width="18" height="12" viewBox="0 0 18 12"><path d="M0 6h16M11 1l5 5-5 5" fill="none" stroke="#fff" stroke-width="1.8"/></svg></a>

    <div class="abs map" role="img" aria-label="Street map showing the hotel location and driving routes in Rhodes Town"></div>
  </section>

  <footer>
    <div class="abs footer"></div>
    <div class="abs brand f-brand"><span class="brand-square"></span><span class="brand-name">Corvena Hotel</span></div>
    <p class="abs f-about">Phasellus nisi sapien, rutrum placerat sapien eu, rhoncus tempus</p>
    <div class="abs socials f-socials"><span></span><span></span><span></span><span></span></div>

    <h3 class="abs f-head" style="left:410px">Information</h3>
    <div class="abs f-info">
      <div><svg width="28" height="28" viewBox="0 0 28 28"><path d="M1 9l8-3 10 3 8-3v19l-8 3-10-3-8 3z" fill="none" stroke="#bf9a47" stroke-width="1.5"/></svg><span>14 Iroon Polytechniou<br>Rhodes, Greece</span></div>
      <div><svg width="28" height="28" viewBox="0 0 28 28"><path d="M2 10l12-8 12 8v15H2z M2 10l12 8 12-8" fill="none" stroke="#bf9a47" stroke-width="1.5"/></svg><span>info@corvenahotel.gr</span></div>
      <div><svg width="28" height="28" viewBox="0 0 32 32"><path d="M8 3l5 7-3 3c2 4 5 7 9 9l3-3 7 5-3 4C15 27 5 17 4 6z" fill="none" stroke="#bf9a47" stroke-width="1.7"/></svg><span>+30 (224) 105 5568</span></div>
    </div>

    <h3 class="abs f-head" style="left:695px">Pages Links</h3>
    <div class="abs f-links"><div>Room Cleaning</div><div>Car Parking</div><div>Swimming pool</div><div>Fitness Gym</div></div>

    <h3 class="abs f-head" style="left:885px">Subscribe</h3>
    <div class="abs sub-field">Email Address</div>
    <div class="abs sub-btn"><svg width="16" height="16" viewBox="0 0 16 16"><path d="M1 8l14-7-4 14-3-5z" fill="none" stroke="#fff" stroke-width="1.4"/></svg></div>

    <div class="abs bottom-line"></div>
    <div class="abs copy">Copyright 2022 <em>Corvena Hotel,</em> All rights reserved.</div>
    <div class="abs legal"><span>FAQ</span><i>|</i><span>Terms of Use</span><i>|</i><span>Privacy Policy</span></div>
    <div class="abs to-top"><svg width="14" height="20" viewBox="0 0 14 20"><path d="M7 20V2M1 8l6-6 6 6" fill="none" stroke="#fff" stroke-width="1.8"/></svg></div>
  </footer>

</div>
</body>
</html>
```